Brekwell Automotive needs a catchy banner design

We need a design for a banner to be displayed on the fence in the outfield of a baseball stadium to show off our company and have people interested in what we do. We need something catchy that's going to attract people to look over at our banner.
We are a
Complete Automotive Service Company
Tires - Service - Repair - Diesel
We are in a Town called Harlow-Creek
(555)314-2609 we would like the phone number to be a descent size so when you are in the stands you can read it.
I have attached what we came up with but like I said we need it to pop more and make the viewer that's looking at it want to look us up.
The Banner size is 24ft long and 10ft tall

```html
<!DOCTYPE html>
<html lang="en">
<head>
<meta charset="utf-8">
<title>Brekwell Automotive – Outfield Banner</title>
<link rel="stylesheet" href="https://fonts.googleapis.com/css2?family=Orbitron:wght@500;700;800&display=swap">
<style>
  :root {
    --bg-dark: #0b0c0f;
    --bg-mid: #16181d;
    --brand-blue: #1f63e6;
    --navy-panel: #172846;
    --text-white: #ffffff;
    --photo-light: #8c9bb2;
    --photo-navy: #2a3f78;
    --photo-grey: #5d6675;
  }
  * { margin: 0; padding: 0; box-sizing: border-box; }
  html, body { width: 1200px; height: 500px; overflow: hidden; background: var(--bg-dark); }
  .banner {
    position: relative;
    width: 1200px;
    height: 500px;
    overflow: hidden;
    background: radial-gradient(ellipse at 75% 45%, var(--bg-mid) 0%, var(--bg-dark) 70%);
    font-family: "Orbitron", sans-serif;
    color: var(--text-white);
  }
  .banner__shapes { position: absolute; inset: 0; }
  .brand-name {
    position: absolute;
    left: 857px;
    top: 104px;
    transform: translateX(-50%);
    display: flex;
    align-items: center;
    gap: 14px;
    font-size: 28px;
    font-weight: 700;
    letter-spacing: 1px;
    white-space: nowrap;
  }
  .brand-name__mark {
    width: 22px;
    height: 22px;
    background: var(--brand-blue);
  }
  .headline {
    position: absolute;
    left: 857px;
    top: 224px;
    transform: translateX(-50%);
    text-align: center;
    font-size: 34px;
    font-weight: 700;
    line-height: 46px;
    letter-spacing: 1.5px;
    white-space: nowrap;
    text-transform: uppercase;
  }
  .services {
    position: absolute;
    left: 857px;
    top: 323px;
    transform: translateX(-50%);
    display: flex;
    align-items: center;
    gap: 11px;
    font-size: 17px;
    font-weight: 700;
    letter-spacing: 1px;
    white-space: nowrap;
    text-transform: uppercase;
  }
  .services__dot {
    width: 10px;
    height: 10px;
    border-radius: 50%;
    background: var(--brand-blue);
  }
  .town {
    position: absolute;
    left: 857px;
    top: 368px;
    transform: translateX(-50%);
    font-size: 26px;
    font-weight: 700;
    letter-spacing: 1.5px;
    white-space: nowrap;
    text-transform: uppercase;
  }
  .phone {
    position: absolute;
    left: 857px;
    top: 414px;
    transform: translateX(-50%);
    font-size: 42px;
    font-weight: 500;
    letter-spacing: 1px;
    white-space: nowrap;
  }
</style>
</head>
<body>
<main class="banner">
  <svg class="banner__shapes" width="1200" height="500" viewBox="0 0 1200 500">
    <defs>
      <linearGradient id="photoTone" x1="0" y1="0" x2="1" y2="1">
        <stop offset="0" stop-color="#8c9bb2"/>
        <stop offset="0.45" stop-color="#2a3f78"/>
        <stop offset="1" stop-color="#5d6675"/>
      </linearGradient>
    </defs>
    <rect class="corner-panel" x="1035" y="-90" width="190" height="190" rx="26"
          transform="rotate(45 1130 5)" fill="#172846" opacity="0.85"/>
    <path class="photo-area" role="img" aria-label="Photo of a mechanic in a navy uniform and work gloves servicing a car engine in a workshop"
          d="M0 0 H630 Q668 0 650 38 L340 430 Q318 456 290 438 L0 188 Z"
          fill="url(#photoTone)"/>
    <rect class="accent-tile" x="-45" y="255" width="230" height="230" rx="28"
          transform="rotate(45 70 370)" fill="#1f63e6" opacity="0.88"/>
  </svg>

  <div class="brand-name"><span class="brand-name__mark"></span>Brekwell Automotive</div>

  <h1 class="headline">Automotive Service<br>Company</h1>

  <div class="services">
    <span>Tires</span><span class="services__dot"></span>
    <span>Service</span><span class="services__dot"></span>
    <span>Repair</span><span class="services__dot"></span>
    <span>Diesel</span>
  </div>

  <div class="town">Harlow-Creek</div>

  <div class="phone">(555)314-2609</div>
</main>
</body>
</html>
```